Looking for a cool & simple business-card-design for digital agency

Hi!

We are a web agency that offers Reputation Management, Vextor & Seo Services and software development. We like cool things, we like innovative styles.

We have uploaded our logo.

Project Deadline Extended Reason: Client does not want any designs with the colorful logo. Please send us submissions ONLY with the blac and white logo. What the client would like to see:1) Back of the card: is a silver logo on a black background2) front of the card with all the data, please use white background and black logo thank you Added Friday, May 8, 2015

Industry/Entity Type

Software

```html
<!DOCTYPE html>
<html lang="en">
<head>
<meta charset="utf-8">
<title>NetVantage Stationery</title>
<link href="https://fonts.googleapis.com/css2?family=Open+Sans:wght@400;600;700&display=swap" rel="stylesheet">
<style>
  :root{
    --bg:#e6e6e6;
    --paper:#ffffff;
    --ink:#111111;
    --ink-soft:#333333;
    --grey:#6b6b6b;
    --silver-1:#f2f2f2;
    --silver-2:#9a9a9a;
    --card:#1c1c1c;
    --card-2:#262626;
    --shadow:0 4px 10px rgba(0,0,0,.25);
  }
  *{margin:0;padding:0;box-sizing:border-box}
  html,body{width:1200px;height:934px;overflow:hidden;background:var(--bg);font-family:"Open Sans",Arial,sans-serif;color:var(--ink)}
  .canvas{position:relative;width:1200px;height:934px}
  .sheet{position:absolute;background:var(--paper);box-shadow:var(--shadow);overflow:hidden}

  .brand{display:flex;align-items:center;gap:6px;font-weight:700;color:var(--ink-soft);white-space:nowrap}
  .brand-square{display:inline-block;background:currentColor;flex:none}

  /* letterhead */
  .letterhead{left:69px;top:83px;width:468px;height:664px}
  .letterhead .edge-top{position:absolute;left:0;top:21px;width:6px;height:61px;background:var(--ink)}
  .letterhead .edge-bottom{position:absolute;right:0;top:580px;width:7px;height:63px;background:var(--ink)}
  .letterhead .brand{position:absolute;left:27px;top:38px;font-size:15px}
  .letterhead .brand-square{width:14px;height:14px}
  .letterhead .company{position:absolute;left:238px;top:43px;font-size:6px;line-height:9px;color:var(--ink-soft)}
  .letterhead .company b{display:block;font-weight:700}
  .contact-list{list-style:none;font-size:6px;line-height:9px;color:var(--ink-soft)}
  .contact-list li{display:flex;align-items:center;gap:5px}
  .contact-list li::before{content:"";width:4px;height:4px;border-radius:50%;background:var(--grey);flex:none}
  .letterhead .contact-list{position:absolute;left:343px;top:43px}

  /* envelope front */
  .env-front{left:565px;top:83px;width:566px;height:257px}
  .env-front .brand{position:absolute;left:29px;top:33px;font-size:21px}
  .env-front .brand-square{width:19px;height:19px}
  .env-front .band{position:absolute;left:0;bottom:0;width:100%;height:16px}

  /* envelope back */
  .env-back{left:565px;top:365px;width:566px;height:256px}
  .env-back .flap{position:absolute;left:0;top:0;width:100%;height:92px}
  .env-back .url{position:absolute;left:0;top:40px;width:100%;text-align:center;color:#e8e8e8;font-size:9px;letter-spacing:2px}
  .env-back .contact-list{position:absolute;top:193px}
  .env-back .col-a{left:160px}
  .env-back .col-b{left:311px}
  .env-back .band{position:absolute;left:0;bottom:0;width:100%;height:8px}

  /* cards */
  .card{position:absolute;top:647px;width:122px;height:204px;box-shadow:var(--shadow);overflow:hidden}
  .card-back{left:565px;background:linear-gradient(160deg,var(--card-2),var(--card))}
  .card-back .brand{position:absolute;left:0;top:88px;width:100%;justify-content:center;color:#e4e4e4;font-size:13px;gap:5px}
  .card-back .brand-square{width:11px;height:11px;background:linear-gradient(180deg,var(--silver-1),var(--silver-2))}

  .card-front{left:726px;background:var(--paper);color:var(--ink)}
  .card-front .mark{position:absolute;left:45px;top:34px;width:32px;height:32px;background:var(--ink)}
  .card-front .person{position:absolute;left:0;top:104px;width:100%;text-align:center}
  .card-front .name{font-size:7.5px;font-weight:700;color:var(--ink)}
  .card-front .role{font-size:5px;color:var(--grey);margin-top:1px}
  .card-front .details{position:absolute;right:10px;top:152px;list-style:none;font-size:4.6px;line-height:8px;text-align:right;color:var(--ink-soft);white-space:nowrap}
  .card-front .details li::after{content:"";display:inline-block;width:3px;height:3px;border-radius:50%;background:var(--ink-soft);margin-left:3px;vertical-align:middle}
  .card-front .strip{position:absolute;left:0;bottom:0;width:100%;height:7px;background:var(--ink)}
</style>
</head>
<body>
<main class="canvas">

  <section class="sheet letterhead" aria-label="Letterhead">
    <span class="edge-top"></span>
    <div class="brand"><span class="brand-square"></span>NetVantage</div>
    <p class="company"><b>NetVantage LLC</b>Your Commercial or office<br>address, pin code</p>
    <ul class="contact-list">
      <li>00.00.00.0000</li>
      <li>yourname@yourwebsite.com</li>
      <li>www.yourwebsite.com</li>
    </ul>
    <span class="edge-bottom"></span>
  </section>

  <section class="sheet env-front" aria-label="Envelope front">
    <div class="brand"><span class="brand-square"></span>NetVantage</div>
    <svg class="band" viewBox="0 0 566 16" preserveAspectRatio="none">
      <rect width="566" height="16" fill="#111"/>
      <polygon points="430,16 470,0 566,0 566,16" fill="#6b6b6b"/>
    </svg>
  </section>

  <section class="sheet env-back" aria-label="Envelope back">
    <svg class="flap" viewBox="0 0 566 92" preserveAspectRatio="none">
      <polygon points="0,0 566,0 526,92 44,92" fill="#111"/>
    </svg>
    <p class="url">www.netvantage.com</p>
    <ul class="contact-list col-a">
      <li>Your Commercial or office address</li>
      <li>00.00.00.0000</li>
    </ul>
    <ul class="contact-list col-b">
      <li>yourname@yourwebsite.com</li>
      <li>www.yourwebsite.com</li>
    </ul>
    <svg class="band" viewBox="0 0 566 8" preserveAspectRatio="none">
      <rect width="566" height="8" fill="#111"/>
      <polygon points="380,8 400,0 566,0 566,8" fill="#6b6b6b"/>
    </svg>
  </section>

  <article class="card card-back" aria-label="Business card back">
    <div class="brand"><span class="brand-square"></span>NetVantage</div>
  </article>

  <article class="card card-front" aria-label="Business card front">
    <span class="mark"></span>
    <div class="person">
      <p class="name">Your Long Name</p>
      <p class="role">Managing Director</p>
    </div>
    <ul class="details">
      <li>Your Commercial or office address</li>
      <li>00.00.00.0000 · 00.00.00.0000</li>
      <li>yourname@yourwebsite.com</li>
      <li>www.yourwebsite.com</li>
    </ul>
    <span class="strip"></span>
  </article>

</main>
</body>
</html>
```